Brake Test Training for Coal Mining

We offer Brake Test Training for Coal Mine workers. It's a legislative requirement that workers who are tasked with performing brake testing have certain competencies to do so. We test Light Vehicles and trailers, Heavy Vehicles and Mobile Mining Equipment like Graders, Scrapers and Dump Trucks.

```html
<!DOCTYPE html>
<html lang="en">
<head>
<meta charset="utf-8">
<title>Brake Test Training – Banner</title>
<link href="https://fonts.googleapis.com/css2?family=Anton&display=swap" rel="stylesheet">
<style>
  :root {
    --navy: #1c4a72;
    --navy-deep: #173f63;
    --yellow: #f6bd0f;
    --white: #ffffff;
    --page: #e9eaec;
  }
  html, body {
    margin: 0;
    padding: 0;
    width: 1200px;
    height: 1200px;
    overflow: hidden;
    background: var(--page);
  }
  .banner {
    position: absolute;
    left: 30px;
    top: 313px;
    width: 1140px;
    height: 573px;
    background: var(--white);
    font-family: "Anton", "Oswald", sans-serif;
  }
  .banner-art {
    position: absolute;
    inset: 0;
    width: 100%;
    height: 100%;
  }
  .brand {
    position: absolute;
    left: 96px;
    top: 80px;
    display: flex;
    align-items: center;
    gap: 16px;
  }
  .brand-mark {
    width: 56px;
    height: 56px;
    border-radius: 50%;
    background: var(--navy);
  }
  .brand-name {
    border-top: 3px solid var(--navy);
    border-bottom: 3px solid var(--yellow);
    padding: 4px 14px 3px;
    color: var(--navy);
    text-align: center;
    line-height: 1.05;
    letter-spacing: 1px;
  }
  .brand-name .line-main { display: block; font-size: 20px; }
  .brand-name .line-sub { display: block; font-size: 11px; letter-spacing: 1.5px; }
  .headline {
    position: absolute;
    left: 104px;
    top: 172px;
    margin: 0;
    color: var(--navy);
    font-weight: 400;
    font-size: 90px;
    line-height: 0.97;
    letter-spacing: -0.5px;
  }
  .audience {
    position: absolute;
    left: 106px;
    top: 360px;
    margin: 0;
    color: var(--yellow);
    font-size: 29px;
    letter-spacing: 0.2px;
  }
  .contact {
    position: absolute;
    left: 103px;
    display: flex;
    align-items: center;
    gap: 18px;
  }
  .contact-phone { top: 418px; color: var(--navy); font-size: 44px; }
  .contact-web { top: 471px; color: var(--yellow); font-size: 38px; }
  .contact-icon {
    width: 39px;
    height: 39px;
    background: var(--navy);
    display: flex;
    align-items: center;
    justify-content: center;
    flex: none;
  }
  .contact-text { line-height: 1; }
</style>
</head>
<body>
  <div class="banner">
    <svg class="banner-art" viewBox="0 0 1026 516" preserveAspectRatio="none" xmlns="http://www.w3.org/2000/svg">
      <defs>
        <linearGradient id="photo-grader" x1="0" y1="0" x2="0" y2="1">
          <stop offset="0" stop-color="#7f9a6a"/>
          <stop offset="0.5" stop-color="#c7a63a"/>
          <stop offset="1" stop-color="#8a4b2c"/>
        </linearGradient>
        <linearGradient id="photo-ute" x1="0" y1="0" x2="0" y2="1">
          <stop offset="0" stop-color="#b9c4cc"/>
          <stop offset="0.5" stop-color="#e8eaeb"/>
          <stop offset="1" stop-color="#6e6f6e"/>
        </linearGradient>
        <linearGradient id="photo-dumptruck" x1="0" y1="0" x2="0" y2="1">
          <stop offset="0" stop-color="#8fa2a8"/>
          <stop offset="0.45" stop-color="#d6b12c"/>
          <stop offset="1" stop-color="#4a4a3a"/>
        </linearGradient>
      </defs>
      <rect class="band-top" x="0" y="0" width="1026" height="22" fill="var(--navy)"/>
      <polygon class="panel-navy" points="656,22 1026,22 1026,497 418,497" fill="var(--navy)"/>
      <polygon class="panel-yellow" points="539,257 840,257 720,497 418,497" fill="var(--yellow)"/>
      <polygon class="panel-navy-right" points="928,22 1026,22 1026,497 713,497 833,257 848,184" fill="var(--navy)"/>
      <g role="img" aria-label="Photo of a yellow motor grader on red earth">
        <polygon points="673,24 928,24 851,177 596,177" fill="url(#photo-grader)"/>
      </g>
      <g role="img" aria-label="Photo of a white mine-spec light vehicle ute">
        <polygon points="593,184 848,184 803,274 769,342 514,342" fill="url(#photo-ute)"/>
      </g>
      <g role="img" aria-label="Photo of a yellow haul dump truck">
        <polygon points="511,348 766,348 718,444 692,497 437,497" fill="url(#photo-dumptruck)"/>
      </g>
      <rect class="band-bottom" x="0" y="497" width="1026" height="19" fill="var(--yellow)"/>
    </svg>

    <div class="brand">
      <div class="brand-mark"></div>
      <div class="brand-name">
        <span class="line-main">RIDGELINE</span>
        <span class="line-sub">OPERATOR TRAINING</span>
      </div>
    </div>

    <h1 class="headline">Brake Test<br>Training</h1>
    <p class="audience">FOR COAL MINE WORKERS</p>

    <div class="contact contact-phone">
      <span class="contact-icon">
        <svg width="24" height="24" viewBox="0 0 24 24" aria-hidden="true">
          <path fill="#fff" d="M6.6 10.8c1.4 2.8 3.8 5.1 6.6 6.6l2.2-2.2c.3-.3.7-.4 1-.2 1.1.4 2.3.6 3.6.6.6 0 1 .4 1 1V20c0 .6-.4 1-1 1C10.6 21 3 13.4 3 4c0-.6.4-1 1-1h3.5c.6 0 1 .4 1 1 0 1.3.2 2.5.6 3.6.1.3 0 .7-.2 1z"/>
        </svg>
      </span>
      <span class="contact-text">1300 555 274</span>
    </div>

    <div class="contact contact-web">
      <span class="contact-icon">
        <svg width="24" height="24" viewBox="0 0 24 24" aria-hidden="true" fill="none" stroke="#fff" stroke-width="1.6">
          <circle cx="12" cy="12" r="9"/>
          <ellipse cx="12" cy="12" rx="4" ry="9"/>
          <line x1="3" y1="12" x2="21" y2="12"/>
          <line x1="4.5" y1="7.5" x2="19.5" y2="7.5"/>
          <line x1="4.5" y1="16.5" x2="19.5" y2="16.5"/>
        </svg>
      </span>
      <span class="contact-text">www.rlot.com.au</span>
    </div>
  </div>
</body>
</html>
```